A private security company called "Tavron Security Services Ltd"

Hello everybody,

We need a web page for a company based in NZ. It is mainly an informative website so it would be wonderful if the designer puts their absolute best into making it a website that I would really appreciate. The website needs to show professionalism and also needs to make our web surfers find the information they need in a click. the company's colour is black and silver, and if those two colours could be integrated into the website it would be absolutely lovely. Please do contact me for any information.

Sincerely,
Dorian Vaskel

Industry/Entity Type

Security

```html
<!DOCTYPE html>
<html lang="en">
<head>
<meta charset="utf-8">
<title>Tavron Security Services Ltd</title>
<link href="https://fonts.googleapis.com/css2?family=Mulish:ital,wght@0,400;0,500;0,600;0,700;1,400&display=swap" rel="stylesheet">
<style>
:root{
  --ink:#2b2b2b;
  --charcoal:#3f3f3f;
  --nav:#2f2f2f;
  --silver:#e6e6e6;
  --silver-dark:#c9c9c9;
  --paper:#f3f3f3;
  --band:#efefef;
  --text:#444;
  --muted:#666;
  --white:#fff;
}
*{margin:0;padding:0;box-sizing:border-box}
html,body{width:850px;height:1200px;overflow:hidden}
body{position:relative;background:var(--white);font-family:"Mulish",sans-serif;color:var(--text)}
.abs{position:absolute}
.top-bg{left:0;top:0;width:850px;height:160px;background:var(--paper)}
.brand{left:53px;top:14px;width:110px;height:66px;text-align:center}
.brand-mark{width:16px;height:16px;background:var(--ink);margin:6px auto 8px}
.brand-name{font-size:17px;font-weight:700;letter-spacing:2px;color:var(--ink);line-height:1}
.brand-sub{font-size:6.5px;font-weight:700;letter-spacing:.3px;color:var(--ink);margin-top:3px}
.call{left:650px;top:30px}
.call svg{position:absolute;left:0;top:2px}
.call-label{position:absolute;left:32px;top:0;font-size:10px;color:var(--muted);white-space:nowrap}
.call-number{position:absolute;left:32px;top:13px;font-size:18px;color:var(--ink);white-space:nowrap}
.nav{left:53px;top:95px;width:745px;height:34px;background:var(--nav);border:1px solid #1c1c1c;display:flex;align-items:center}
.nav a{color:var(--white);text-decoration:none;font-size:10.5px;font-weight:500;margin-left:15px;margin-right:15px}
.nav a:first-child{margin-left:15px}
.enquire{position:absolute;right:0;top:0;width:148px;height:32px;background:var(--silver);display:flex;align-items:center;gap:10px;padding-left:12px;font-size:14px;color:var(--ink);font-weight:500}
.hero{left:53px;top:136px;width:745px;height:283px;border:2px solid var(--silver);background:linear-gradient(90deg,#cfd9e4 0%,#a9b6c4 35%,#d7b35a 65%,#e6c56b 100%)}
.caption{left:425px;top:213px;width:383px;height:129px;background:rgba(245,245,245,.95);box-shadow:0 2px 4px rgba(0,0,0,.2);padding:10px 16px}
.caption h1{font-weight:500;font-size:24px;line-height:24px;color:var(--ink)}
.caption p{font-size:12px;line-height:18.5px;color:var(--muted);margin-top:10px}
.dots{left:406px;top:401px;display:flex;gap:3px}
.dots span{width:7px;height:7px;border-radius:50%;background:#666}
.dots span:first-child{background:#111}
.services{left:0;top:442px;width:850px;height:317px;background:var(--charcoal)}
.services h2{position:absolute;left:0;top:21px;width:850px;text-align:center;color:var(--white);font-weight:500;font-size:19px}
.card{top:62px;width:172px}
.card .photo{height:110px}
.card h3{font-weight:500;font-size:14px;color:var(--white);margin-top:15px}
.card p{font-size:9px;line-height:15px;color:#ddd;margin-top:5px}
.btn-light,.btn-dark{display:inline-block;font-size:8.5px;font-weight:600;padding:0 10px;height:25px;line-height:25px;width:78px;text-align:center}
.btn-light{background:var(--white);color:var(--ink);margin-top:13px}
.btn-dark{background:var(--nav);color:var(--white)}
.about{left:53px;top:785px;width:492px}
.about h2{font-weight:500;font-size:19px;color:var(--ink)}
.about p{font-size:9px;line-height:15.2px;color:var(--text);margin-top:10px}
.about p+p{margin-top:5px}
.about .btn-dark{margin-top:20px}
.about-photo{left:563px;top:790px;width:235px;height:180px;border:1px solid var(--silver-dark);background:linear-gradient(120deg,#d8d6d0 0%,#7a7f86 45%,#e2693a 75%,#c9c9c9 100%)}
.trust-band{left:0;top:990px;width:850px;height:122px;background:var(--band);border-bottom:1px solid #c3c3c3}
.trust{left:53px;top:1009px;width:430px}
.trust h3,.testi h3{font-weight:500;font-size:14px;color:var(--ink)}
.trust p{font-size:9px;line-height:15px;margin-top:7px}
.partners{display:flex;gap:18px;margin-top:10px;font-size:13px;font-weight:600;color:var(--ink)}
.divider{left:495px;top:1013px;width:1px;height:91px;background:#ccc}
.testi{left:522px;top:1009px;width:280px}
.testi blockquote{font-size:9px;font-style:italic;line-height:15px;color:var(--text);margin-top:7px}
.testi blockquote b{font-style:normal;font-size:16px;color:#999;margin-right:4px;vertical-align:-3px}
.testi cite{display:block;font-size:8.5px;color:var(--muted);margin-top:6px}
.arrows{left:778px;top:1008px;font-size:12px;color:var(--ink);letter-spacing:6px}
.footer-bg{left:0;top:1113px;width:850px;height:87px;background:var(--paper)}
.foot-brand{left:53px;top:1124px;width:48px;text-align:center}
.foot-brand .brand-mark{width:10px;height:10px;margin:0 auto 4px}
.foot-brand .brand-name{font-size:8px;letter-spacing:1px}
.copyright{left:53px;top:1168px;font-size:8px;color:var(--muted)}
.connect{left:702px;top:1125px;font-size:10px;color:var(--ink)}
.social{left:702px;top:1145px;display:flex;gap:3px}
.social span{width:22px;height:22px;border-radius:50%}
</style>
</head>
<body>
<div class="abs top-bg"></div>

<header>
  <div class="abs brand">
    <div class="brand-mark"></div>
    <div class="brand-name">TAVRON</div>
    <div class="brand-sub">SECURITY SERVICES LTD.</div>
  </div>
  <div class="abs call">
    <svg width="24" height="18" viewBox="0 0 24 18" aria-hidden="true"><path d="M1 6c0-3 5-5 11-5s11 2 11 5v2h-6V6H7v2H1z" fill="#888"/><rect x="4" y="9" width="16" height="8" rx="1" fill="#888"/><circle cx="12" cy="13" r="2.3" fill="#f3f3f3"/></svg>
    <div class="call-label">Call Us Today:</div>
    <div class="call-number">0800 555 0142</div>
  </div>
  <nav class="abs nav">
    <a href="#">HOME</a><a href="#">ABOUT US</a><a href="#">SERVICES</a><a href="#">LATEST NEWS</a><a href="#">TESTIMONIALS</a><a href="#">BLOG</a><a href="#">CONTACT US</a>
    <div class="enquire">
      <svg width="18" height="12" viewBox="0 0 18 12" aria-hidden="true"><rect x=".5" y=".5" width="17" height="11" fill="#fff" stroke="#999"/><path d="M.5 .5 9 7l8.5-6.5" fill="none" stroke="#999"/></svg>
      ENQUIRE NOW
    </div>
  </nav>
</header>

<section>
  <div class="abs hero" role="img" aria-label="Security guard in uniform speaking into a radio in front of a yellow steel bridge"></div>
  <div class="abs caption">
    <h1>Lorem ipsum dolor sit amet consectetur adipiscing</h1>
    <p>Duis aute irure dolor in reprehenderit in voluptate velit esse cillum dolore euugiat nulla pariatur. Nemo enim ipsam voluptatem quia voluptas.</p>
  </div>
  <div class="abs dots"><span></span><span></span><span></span><span></span></div>
</section>

<section class="abs services">
  <h2>Our Services</h2>
  <div class="abs card" style="left:52px">
    <div class="photo" role="img" aria-label="Detection dog inspecting a bag" style="background:linear-gradient(135deg,#6c6c6c,#b8b2a4)"></div>
    <h3>Services Heading</h3>
    <p>Lorem ipsum dolor sit amet, consectetur adipisicing eitseo eiusmod tempor incididunt ut labore et dolore magna aliqua.</p>
    <span class="btn-light">READ MORE ››</span>
  </div>
  <div class="abs card" style="left:244px">
    <div class="photo" role="img" aria-label="Guard in high-visibility vest on the phone" style="background:linear-gradient(135deg,#8a8f96,#c7d24a 55%,#3a3a3a)"></div>
    <h3>Services Heading</h3>
    <p>Lorem ipsum dolor sit amet, consectetur adipisicing eitseo eiusmod tempor incididunt ut labore et dolore magna aliqua.</p>
    <span class="btn-light">READ MORE ››</span>
  </div>
  <div class="abs card" style="left:435px">
    <div class="photo" role="img" aria-label="Uniformed officer holding a red radio" style="background:linear-gradient(135deg,#4f6b3a,#8a6a4c 55%,#5a5236)"></div>
    <h3>Services Heading</h3>
    <p>Lorem ipsum dolor sit amet, consectetur adipisicing eitseo eiusmod tempor incididunt ut labore et dolore magna aliqua.</p>
    <span class="btn-light">READ MORE ››</span>
  </div>
  <div class="abs card" style="left:626px">
    <div class="photo" role="img" aria-label="Agent in suit speaking into a radio" style="background:linear-gradient(135deg,#8b93a3,#c9a996 50%,#2c3140)"></div>
    <h3>Services Heading</h3>
    <p>Lorem ipsum dolor sit amet, consectetur adipisicing eitseo eiusmod tempor incididunt ut labore et dolore magna aliqua.</p>
    <span class="btn-light">READ MORE ››</span>
  </div>
</section>

<section>
  <div class="abs about">
    <h2>About Our Company</h2>
    <p>Aliquam molestie, mi et imperdiet euismod, dui purus auctor tellus, et interdum lacus lectus et ante. Sed accumsan sollicitudin sapien, sit amet adipiscing turpis gravida ac. In congue, neque ac lobortis volutpat, libero mauris varius mi, vitae suscipit ipsum ligula vitae risus. Duis aliquam nibh a dui iaculis viverra id a velit. Vivamus egestas risus in magna varius commodo. Sed semper viverra egestas. Etiam pretium porttitor lectus, vel ornare neque porta volutpat.</p>
    <p>Ut et scelerisque ante. Donec erat purus, faucibus vitae congue vel, porttitor nec lectus. Aenean a nibh eget turpis vehicula tempus ac sed massa. Vestibulum dolor nulla, ultrices ac tincidunt sed, laoreet non est. Suspendisse lobortis turpis in odio blandit ac interdum lorem euismod. Etiam risus massa, vulputate eu pellentesque et, consectetur a neque.</p>
    <span class="btn-dark">READ MORE ››</span>
  </div>
  <div class="abs about-photo" role="img" aria-label="Security operator in orange vest monitoring CCTV screens"></div>
</section>

<section>
  <div class="abs trust-band"></div>
  <div class="abs trust">
    <h3>Trusted By</h3>
    <p>Suspendisse lobortis turpis in odio blandit ac interdum lorem euismod. Etiam risus massa, vulputate eu pellentesque et, consectetur a neque.</p>
    <div class="partners"><span>Brookfare</span><span>Orbitly</span><span>Netlace</span><span>Ledgera</span><span>Printova</span><span>Telvia</span></div>
  </div>
  <div class="abs divider"></div>
  <div class="abs testi">
    <h3>Testimonials</h3>
    <blockquote><b>“</b>Vestibulum dolor nulla, ultrices ac tincidunt sed, laoreet non est. Suspendisse lobortis turpis in odio blandit ac interdum lorem euismod....</blockquote>
    <cite>-Lena Marrow</cite>
  </div>
  <div class="abs arrows">‹›</div>
</section>

<footer>
  <div class="abs footer-bg"></div>
  <div class="abs foot-brand">
    <div class="brand-mark"></div>
    <div class="brand-name">TAVRON</div>
  </div>
  <div class="abs copyright">Copyright © 2014. All Right Reserved</div>
  <div class="abs connect">Connect Us:</div>
  <div class="abs social">
    <span style="background:#3b5a96"></span><span style="background:#2f9ee0"></span><span style="background:#d8332a"></span><span style="background:#444"></span>
  </div>
</footer>
</body>
</html>
```